Business Card Design for Occupational Medicine Start Up Company

We need to design a professional business card. We are a healthcare company providing occupational medicine services to blue collar industries. We are professional, efficient and high quality service providers.

Target Market(s)

Blue Collar Industry: Shipbuilding, Ports, Trucking Companies; The Executives and Safety Officers for these companies

Industry/Entity Type

Healthcare

Contact Information for Business Card

Logo, Name, Title, Email, Phone

Other font styles liked:
• Please match our Brand Guide

Requirements
Must have
• Our Company Colors and Logo

```html
<!DOCTYPE html>
<html lang="en">
<head>
<meta charset="utf-8">
<title>Crewline Clinics – Business Card</title>
<link href="https://fonts.googleapis.com/css2?family=Montserrat:wght@400;500;600;700&display=swap" rel="stylesheet">
<style>
  :root {
    --page-bg: #e9e6e1;
    --card-bg: #fbfaf7;
    --card-edge: #dcd8d0;
    --orange: #e0a23e;
    --navy: #2d2f6b;
    --teal: #2a9bb0;
    --text-grey: #3c3c46;
    --divider: #c9a06a;
  }
  * { margin: 0; padding: 0; box-sizing: border-box; }
  html, body {
    width: 1200px; height: 1200px; overflow: hidden;
    background: var(--page-bg);
    font-family: "Montserrat", sans-serif;
  }
  .business-card {
    position: absolute; left: 60px; top: 305px;
    width: 1080px; height: 590px;
    background: var(--card-bg);
    border: 1px solid var(--card-edge);
    border-radius: 30px;
    overflow: hidden;
    box-shadow: 0 10px 30px rgba(0,0,0,0.08);
  }
  .stripe { position: absolute; left: 0; width: 100%; }
  .stripe-orange { top: 0; height: 36px; background: var(--orange); }
  .stripe-navy { top: 36px; height: 38px; background: var(--navy); }
  .stripe-teal { top: 74px; height: 37px; background: var(--teal); }
  .brand-notch {
    position: absolute; left: 470px; top: 62px;
    width: 140px; height: 140px; border-radius: 50%;
    background: var(--card-bg);
  }
  .brand-dot {
    position: absolute; left: 490px; top: 82px;
    width: 100px; height: 100px; border-radius: 50%;
    background: var(--navy);
  }
  .brand-name {
    position: absolute; left: 0; top: 226px; width: 100%;
    text-align: center;
    font-weight: 600; font-size: 44px; letter-spacing: 1px;
    color: var(--navy);
  }
  .person {
    position: absolute; right: 596px; top: 372px;
    text-align: right;
  }
  .person-name {
    font-weight: 700; font-size: 35px; letter-spacing: 1px;
    color: var(--navy);
  }
  .person-title {
    margin-top: 10px;
    font-weight: 400; font-size: 25px; color: var(--text-grey);
  }
  .divider {
    position: absolute; left: 532px; top: 405px;
    width: 2px; height: 110px; background: var(--divider);
  }
  .contact-list {
    position: absolute; left: 566px; top: 404px;
    list-style: none;
  }
  .contact-item {
    display: flex; align-items: center;
    height: 39px;
    font-size: 25px; font-weight: 500; color: var(--text-grey);
  }
  .contact-icon { width: 24px; height: 24px; margin-right: 16px; flex: none; }
</style>
</head>
<body>
  <div class="business-card">
    <div class="stripe stripe-orange"></div>
    <div class="stripe stripe-navy"></div>
    <div class="stripe stripe-teal"></div>
    <div class="brand-notch"></div>
    <div class="brand-dot"></div>
    <div class="brand-name">CREWLINE CLINICS</div>

    <div class="person">
      <div class="person-name">MARK ELLISON</div>
      <div class="person-title">President</div>
    </div>
    <div class="divider"></div>

    <ul class="contact-list">
      <li class="contact-item">
        <svg class="contact-icon" viewBox="0 0 24 24" aria-hidden="true">
          <path fill="var(--teal)" d="M6.6 10.8a15.1 15.1 0 0 0 6.6 6.6l2.2-2.2c.3-.3.7-.4 1-.2 1.1.4 2.3.6 3.6.6.6 0 1 .4 1 1V20c0 .6-.4 1-1 1A17 17 0 0 1 3 4c0-.6.4-1 1-1h3.5c.6 0 1 .4 1 1 0 1.3.2 2.5.6 3.6.1.3 0 .7-.2 1l-2.3 2.2z"/>
        </svg>
        555-014-2287
      </li>
      <li class="contact-item">
        <svg class="contact-icon" viewBox="0 0 24 24" aria-hidden="true">
          <rect x="2" y="5" width="20" height="14" rx="2" fill="var(--teal)"/>
          <path d="M3 6l9 7 9-7" fill="none" stroke="var(--card-bg)" stroke-width="1.6"/>
        </svg>
        mark@crewlineclinics.com
      </li>
      <li class="contact-item">
        <svg class="contact-icon" viewBox="0 0 24 24" aria-hidden="true">
          <circle cx="12" cy="12" r="10" fill="var(--teal)"/>
          <ellipse cx="12" cy="12" rx="4" ry="10" fill="none" stroke="var(--card-bg)" stroke-width="1.4"/>
          <path d="M2 12h20" stroke="var(--card-bg)" stroke-width="1.4"/>
        </svg>
        www.crewlineclinics.com
      </li>
    </ul>
  </div>
</body>
</html>
```